Professional Engineering Web Design

Project Brief: Website Redesign for Mechanical Design Consultancy
Project Overview
I want to update and improve my current website to create a more professional, modern, and high-credibility online presence for my mechanical design consultancy.

Current site: https://valtorix.design/

The new website must communicate expertise, precision, and trust—matching the standard of top engineering and product design agencies.

Reference Websites (Style + Structure Inspiration)
These represent the quality, cleanliness, and professionalism I want to achieve:

https://plinthwaredesign.com/
https://www.sorvane.com/
https://bramlow-uk.com/
Brand Look
Professional, modern, engineering-focused aesthetic
Clean layouts and strong typography
High-quality imagery conveying precision, innovation, and mechanical expertise
Colour scheme and styling must follow my existing logo (attached in project)
Platform Requirements
The website must be built on WordPress
Should use a clean, flexible theme or modern page builder (Elementor, Gutenberg, Bricks, or similar)
Avoid overly complex custom coding so I can easily edit content later
Final deliverable must allow me to manage and update content without developer assistance
Functionality
Fast-loading, lightweight, and smooth user experience
Clean animations and transitions similar to the reference sites
Fully mobile responsive
Clear navigation and strong visual hierarchy
Contact forms optimised for lead generation
Optional: subtle scroll effects, case study sliders, icon animations, etc.
SEO Aspirations
Developer should recommend and implement a modern SEO strategy
Proper on-page SEO setup (titles, meta, schema, alt tags, heading structure)
Optimised site architecture for ranking and crawling
Aim: Generate leads through improved visibility and keyword targeting
Optional but useful: Google Analytics, Google Search Console setup
User Journeys
(Recommended structure)

The site should be crafted around clear, intuitive journeys for each type of visitor:

Potential new clients
Quickly understand what services I offer
View examples of past work / case studies
See credibility indicators (process, expertise, industries served)
Easily contact me or request a project discussion
Returning clients
Access updated portfolio items
Find contact details or book follow-up work easily
General visitors discovering through SEO
Be guided to core service areas
Understand my value proposition quickly
Be invited to learn more or make contact
The developer should design the structure to support these journeys smoothly.

Maintenance Expectations
Website will be maintained by me, so it should be easy to update using relatively basic WordPress skills
Use modular templates and simple backend structure
Avoid unnecessary plugins
Provide brief handover documentation if required
Hosting Preferences
Site is currently hosted via a family member
Open to discussing moving to a paid, reliable hosting provider if preferable for performance and maintainability
Developer may advise on the best hosting setup for WordPress
Content
Most content can be taken from the existing website
Developer is welcome to suggest improvements to structure, layout, and imagery
Must remain easy for me to edit or add new content later (e.g., new projects)
Deliverables
Fully built WordPress website
Clean, professional, modern design inspired by the reference sites
Mobile-responsive across all devices
SEO-ready structure and optimisations
Transfer of website and admin rights
Any design assets, templates, or documentation used

```html
<!DOCTYPE html>
<html lang="en">
<head>
<meta charset="utf-8">
<title>Valtorix Design — Mechanical CAD Design</title>
<link href="https://fonts.googleapis.com/css2?family=Inter:wght@300;400;500;600&display=swap" rel="stylesheet">
<style>
:root{
  --blue:#2c55e6;
  --blue-deep:#1f45d6;
  --blue-soft:#a9b9f3;
  --ink:#111318;
  --grey:#6b6e76;
  --line:#d9dce3;
  --pale:#f1f3fb;
  --white:#ffffff;
}
*{margin:0;padding:0;box-sizing:border-box}
html,body{width:1200px;height:4069px;overflow:hidden}
body{font-family:'Inter',sans-serif;color:var(--ink);background:var(--white);position:relative}
.abs{position:absolute}
.accent{color:var(--blue)}
.muted{color:var(--grey)}

/* header + hero */
.hero{left:0;top:0;width:1200px;height:600px;background:linear-gradient(100deg,#f4f5fb 0%,#eef0fa 45%,#e3e7f6 100%);overflow:hidden}
.hero-visual{right:0;top:130px;width:600px;height:470px;background:radial-gradient(ellipse at 55% 55%,#b9bfcc 0%,#d6dae3 35%,rgba(228,231,242,0) 72%)}
.brand{display:flex;align-items:center;gap:14px}
.brand-mark{width:66px;height:66px;border-radius:50%;background:var(--blue)}
.brand-name{font-size:44px;font-weight:500;color:var(--blue);letter-spacing:2px}
.nav{left:376px;top:74px;display:flex;gap:44px;font-size:15px}
.nav a{color:var(--ink);text-decoration:none}
.nav a.current{color:var(--blue);text-decoration:underline;text-underline-offset:4px}
.search{left:893px;top:76px}
.btn{display:inline-flex;align-items:center;justify-content:center;gap:12px;font-size:15px;font-weight:500;text-decoration:none}
.btn-outline{border:1.5px solid var(--blue);color:var(--blue);background:var(--white);border-radius:3px}
.btn-solid{background:var(--blue);color:var(--white);border-radius:3px;box-shadow:5px 5px 0 var(--blue-soft)}
.hero h1{left:111px;top:238px;font-size:49px;font-weight:500;letter-spacing:-.5px}
.hero .sub{left:111px;top:304px;font-size:32px;font-weight:400}

/* welcome */
.decor-ring{left:-120px;top:708px;width:240px;height:240px;border-radius:50%;background:#c6d0f6}
.welcome-label{left:186px;top:728px;font-size:25px}
.statement{left:186px;top:790px;font-size:33px;line-height:38px;font-weight:400;letter-spacing:-.3px}
.card{background:var(--white);border:1px solid var(--line);border-radius:3px;box-shadow:6px 6px 0 #e7e9f0}
.card.active{box-shadow:6px 6px 0 var(--blue)}
.svc{padding:36px 26px}
.svc-head{display:flex;gap:16px;align-items:flex-start}
.svc-title{font-size:26px;line-height:30px}
.svc-body{margin-top:34px;font-size:14px;line-height:26px}
.go{position:absolute;right:24px;bottom:24px;width:36px;height:36px}

/* portfolio */
.portfolio{left:11px;top:1421px;width:1178px;height:727px;background:var(--blue);border-radius:4px}
.p-icon{left:112px;top:1504px;width:42px;height:42px;border-radius:50%;border:6px solid var(--white)}
.p-label{left:183px;top:1510px;font-size:26px;color:var(--white)}
.p-sub{left:186px;top:1574px;font-size:31px;color:var(--white)}
.work{background:var(--white);border-radius:3px;display:flex;gap:24px;padding:26px 24px}
.thumb{width:98px;height:94px;border-radius:3px;flex:none}
.work-title{font-size:27px;line-height:31px;margin-top:26px}

/* about */
.about-title{left:384px;top:2234px;font-size:27px}
.portrait{left:112px;top:2283px;width:193px;height:191px;background:linear-gradient(160deg,#8a8f99 0%,#5a5f6b 55%,#2c3550 100%);box-shadow:8px 8px 0 #e7e9f0}
.socials{display:flex;gap:14px}
.socials span{width:20px;height:20px;border-radius:50%;background:var(--blue)}
.lead{left:384px;top:2296px;font-size:33px;line-height:38px;letter-spacing:-.3px}
.about-copy{left:384px;top:2392px;font-size:15px;line-height:26px;width:720px}

/* testimonials */
.voices{left:0;top:2653px;width:1200px;height:742px;background:linear-gradient(180deg,#ffffff 0%,#f1f3fb 40%,#f4f5fb 100%)}
.v-label{left:172px;top:2756px;font-size:26px}
.v-sub{left:174px;top:2808px;font-size:32px}
.quote-card{left:308px;top:2918px;width:587px;height:335px;padding:60px 40px 0;text-align:center}
.quote{font-size:15px;font-style:italic;line-height:29px}
.q-name{font-size:21px;color:var(--blue);margin-top:26px}
.q-role{font-size:15px;margin-top:4px}
.ghost{top:2969px;width:310px;height:252px;background:var(--white);opacity:.55;font-size:15px;font-style:italic;line-height:29px;color:#8a8d95;overflow:hidden}
.ghost .g-name{font-style:normal;text-align:center;color:var(--blue);font-size:20px;margin-top:20px}
.ghost .g-role{font-style:normal;text-align:center;font-size:15px}
.avatar{width:64px;height:64px;border-radius:50%;display:flex;align-items:center;justify-content:center;font-size:26px}
.dots{left:569px;top:3283px;display:flex;gap:7px}
.dots span{width:10px;height:10px;border-radius:50%;background:#b9bcc6}
.dots span.on{background:var(--blue)}

/* cta */
.cta{left:0;top:3395px;width:1200px;height:366px;background:linear-gradient(120deg,#4467ea 0%,#2c55e6 55%,#3b5ee8 100%);color:var(--white);text-align:center}
.cta-label{top:98px;width:1200px;font-size:26px}
.cta-title{top:140px;width:1200px;font-size:33px}

/* footer */
.foot-blurb{left:636px;top:3880px;font-size:15px;line-height:26px}
.foot-links{left:111px;top:3958px;display:flex;gap:28px;font-size:15px}
.foot-links a{color:var(--ink);text-decoration:none}
.contact{top:3958px;font-size:15px;display:flex;align-items:center;gap:10px}
.copy{left:111px;top:4018px;font-size:13px}
.follow{left:636px;top:4012px;display:flex;align-items:center;gap:24px;font-size:21px;color:var(--blue)}
</style>
</head>
<body>

<section class="hero abs">
  <div class="hero-visual abs" role="img" aria-label="Machined steel flange over a faint engineering drawing"></div>
  <h1 class="abs">Mechanical <span class="accent">CAD</span> Design</h1>
  <p class="sub abs">Cutting Edge Engineering</p>
  <a class="btn btn-solid abs" style="left:111px;top:406px;width:176px;height:47px" href="#">Get Started
    <svg width="16" height="12" viewBox="0 0 16 12"><path d="M1 6h13M9 1l5 5-5 5" fill="none" stroke="#fff" stroke-width="1.6"/></svg></a>
</section>

<header>
  <div class="brand abs" style="left:76px;top:52px">
    <span class="brand-mark"></span><span class="brand-name">valtorix</span>
  </div>
  <nav class="nav abs">
    <a class="current" href="#">Home</a><a href="#">Work Portfolio</a><a href="#">Our Services</a><a href="#">Contact Us</a>
  </nav>
  <svg class="search abs" width="18" height="18" viewBox="0 0 18 18"><circle cx="7.5" cy="7.5" r="5.5" fill="none" stroke="#2c55e6" stroke-width="1.8"/><path d="M12 12l5 5" stroke="#2c55e6" stroke-width="1.8"/></svg>
  <a class="btn btn-outline abs" style="left:943px;top:60px;width:173px;height:49px" href="#">Get in Touch
    <svg width="16" height="12" viewBox="0 0 16 12"><path d="M1 6h13M9 1l5 5-5 5" fill="none" stroke="#2c55e6" stroke-width="1.6"/></svg></a>
</header>

<section class="welcome">
  <div class="decor-ring abs"></div>
  <p class="welcome-label abs">Welcome to <span class="accent">Valtorix Design</span></p>
  <p class="statement abs">We are a UK based design consultancy offering<br>a comprehensive <span class="accent">mechanical and product design</span><br><span class="muted">service from initial concepts through to<br>full volume production</span></p>

  <article class="card svc abs" style="left:111px;top:1034px;width:312px;height:272px">
    <div class="svc-head">
      <svg width="56" height="50" viewBox="0 0 56 50"><rect x="4" y="14" width="26" height="16" rx="3" transform="rotate(-35 17 22)" fill="none" stroke="#2c55e6" stroke-width="2"/><rect x="24" y="20" width="26" height="16" rx="3" transform="rotate(-35 37 28)" fill="none" stroke="#2c55e6" stroke-width="2"/></svg>
      <div class="svc-title">Bespoke<br><span class="accent">Product Design</span></div>
    </div>
    <p class="svc-body">Innovative design from concept<br>through the full development life<br>cycle phases.</p>
    <svg class="go" viewBox="0 0 36 36"><circle cx="18" cy="18" r="16" fill="none" stroke="#9ea1a9" stroke-width="1.4"/><path d="M11 18h13M19 13l5 5-5 5" fill="none" stroke="#9ea1a9" stroke-width="1.4"/></svg>
  </article>

  <article class="card svc abs" style="left:442px;top:992px;width:313px;height:271px">
    <div class="svc-head">
      <svg width="56" height="50" viewBox="0 0 56 50"><path d="M28 6 52 18 28 30 4 18z" fill="none" stroke="#2c55e6" stroke-width="2"/><path d="M4 26l24 12 24-12M4 33l24 12 24-12" fill="none" stroke="#2c55e6" stroke-width="2"/></svg>
      <div class="svc-title">3D Modelling<br><span class="accent">&amp; Drawings</span></div>
    </div>
    <p class="svc-body">We create 3D CAD, 2D engineering<br>drawings and photorealistic renders<br>for your needs.</p>
    <svg class="go" viewBox="0 0 36 36"><circle cx="18" cy="18" r="16" fill="none" stroke="#9ea1a9" stroke-width="1.4"/><path d="M11 18h13M19 13l5 5-5 5" fill="none" stroke="#9ea1a9" stroke-width="1.4"/></svg>
  </article>

  <article class="card active svc abs" style="left:772px;top:949px;width:318px;height:275px">
    <div class="svc-head">
      <svg width="56" height="56" viewBox="0 0 56 56"><path d="M28 4 50 16v24L28 52 6 40V16z M6 16l22 12 22-12 M28 28v24" fill="none" stroke="#2c55e6" stroke-width="2"/></svg>
      <div class="svc-title">Design for<br><span class="accent">Manufacture</span></div>
    </div>
    <p class="svc-body">We work in Creating designs<br>optimised for prototype and also<br>production manufacture.</p>
    <svg class="go" viewBox="0 0 36 36"><circle cx="18" cy="18" r="17" fill="#2c55e6"/><path d="M11 18h13M19 13l5 5-5 5" fill="none" stroke="#fff" stroke-width="1.6"/></svg>
  </article>
</section>

<section class="portfolio abs"></section>
<div class="p-icon abs"></div>
<p class="p-label abs">Our Work Portfolio</p>
<p class="p-sub abs">A Small Selection of Our Previous Projects</p>

<article class="work abs" style="left:104px;top:1666px;width:321px;height:174px">
  <div class="thumb" role="img" aria-label="Render of a three-piece alloy wheel" style="background:radial-gradient(circle,#c9ccd2,#f2f3f5)"></div>
  <div class="work-title">3-Piece<br><span class="accent">Alloy Wheels</span></div>
  <svg class="go" viewBox="0 0 36 36"><circle cx="18" cy="18" r="17" fill="#2c55e6"/><path d="M11 18h13M19 13l5 5-5 5" fill="none" stroke="#fff" stroke-width="1.6"/></svg>
</article>
<article class="work abs" style="left:444px;top:1666px;width:320px;height:174px">
  <div class="thumb" role="img" aria-label="Render of a go-kart simulator rig" style="background:linear-gradient(160deg,#eceef0,#9aa0a6)"></div>
  <div class="work-title">Go-Kart<br><span class="accent">Simulator</span></div>
  <svg class="go" viewBox="0 0 36 36"><circle cx="18" cy="18" r="16" fill="none" stroke="#9ea1a9" stroke-width="1.4"/><path d="M11 18h13M19 13l5 5-5 5" fill="none" stroke="#9ea1a9" stroke-width="1.4"/></svg>
</article>
<article class="work abs" style="left:778px;top:1666px;width:321px;height:174px">
  <div class="thumb" role="img" aria-label="Render of a landscape measuring device" style="background:linear-gradient(160deg,#d8d9dc,#6b5a30)"></div>
  <div class="work-title">Landscape<br><span class="accent">Measurer</span></div>
  <svg class="go" viewBox="0 0 36 36"><circle cx="18" cy="18" r="16" fill="none" stroke="#9ea1a9" stroke-width="1.4"/><path d="M11 18h13M19 13l5 5-5 5" fill="none" stroke="#9ea1a9" stroke-width="1.4"/></svg>
</article>
<article class="work abs" style="left:111px;top:1857px;width:314px;height:172px">
  <div class="thumb" role="img" aria-label="Render of a dual clutch engine" style="background:linear-gradient(160deg,#8d8a86,#3f3d3b)"></div>
  <div class="work-title">Dual Clutch<br><span class="accent">Engine</span></div>
  <svg class="go" viewBox="0 0 36 36"><circle cx="18" cy="18" r="16" fill="none" stroke="#9ea1a9" stroke-width="1.4"/><path d="M11 18h13M19 13l5 5-5 5" fill="none" stroke="#9ea1a9" stroke-width="1.4"/></svg>
</article>
<article class="work abs" style="left:444px;top:1857px;width:320px;height:172px">
  <div class="thumb" role="img" aria-label="Render of electrical switchgear gears" style="background:radial-gradient(circle,#d7d8da,#4a4b4e)"></div>
  <div class="work-title">Electrical<br><span class="accent">Switchgear</span></div>
  <svg class="go" viewBox="0 0 36 36"><circle cx="18" cy="18" r="16" fill="none" stroke="#9ea1a9" stroke-width="1.4"/><path d="M11 18h13M19 13l5 5-5 5" fill="none" stroke="#9ea1a9" stroke-width="1.4"/></svg>
</article>
<article class="work abs" style="left:778px;top:1857px;width:321px;height:172px">
  <div class="thumb" role="img" aria-label="Render of a luxury pen" style="background:linear-gradient(90deg,#2b2a28,#8a7a5a,#2b2a28)"></div>
  <div class="work-title">MORVIA<br><span class="accent">Luxury Pen</span></div>
  <svg class="go" viewBox="0 0 36 36"><circle cx="18" cy="18" r="16" fill="none" stroke="#9ea1a9" stroke-width="1.4"/><path d="M11 18h13M19 13l5 5-5 5" fill="none" stroke="#9ea1a9" stroke-width="1.4"/></svg>
</article>

<section class="about">
  <p class="about-title abs">Who We Are at <span class="accent">Valtorix Design</span></p>
  <div class="portrait abs" role="img" aria-label="Portrait of the chief engineer"></div>
  <div class="socials abs" style="left:150px;top:2511px"><span></span><span></span><span></span><span></span></div>
  <svg class="abs" style="left:336px;top:2304px" width="40" height="20" viewBox="0 0 40 20"><path d="M38 12C28 2 14 2 4 10M4 10l8-6M4 10l9 3" fill="none" stroke="#a9b9f3" stroke-width="2"/></svg>
  <p class="lead abs"><span class="accent">Aldric Penwell</span> is the Chief Engineer here<br><span class="muted">at Valtorix Design</span></p>
  <p class="about-copy abs">He has 11 years experience working as a mechanical design engineer in multiple industries including high performance automotive, consumer products, medical, industrial plus many more.<br>He has worked in multiple roles across a wide range of products.</p>
  <a class="btn btn-solid abs" style="left:387px;top:2507px;width:259px;height:46px" href="#">Tell Us About Your Ideas
    <svg width="16" height="12" viewBox="0 0 16 12"><path d="M1 6h13M9 1l5 5-5 5" fill="none" stroke="#fff" stroke-width="1.6"/></svg></a>
</section>

<section class="voices abs"></section>
<svg class="abs" style="left:106px;top:2750px" width="46" height="44" viewBox="0 0 46 44"><path d="M23 2l6 14 15 1-11 10 4 15-14-8-14 8 4-15L2 17l15-1z" fill="#2c55e6"/></svg>
<p class="v-label abs">What <span class="accent">People</span> Have to Say</p>
<p class="v-sub abs">Feedback from some of Our <span class="accent">Recent Customers</span></p>

<div class="ghost abs" style="left:-8px;padding:24px 20px 0 0">
  <p style="margin-left:-4px">was an excellent teammate on my project. He brought valuable knowledge to every design decision and stayed flexible throughout, regularly available to talk through problems, and kept everything on schedule.</p>
  <p class="g-name">Tamsin</p><p class="g-role">Client</p>
</div>
<div class="ghost abs" style="left:898px;padding:24px 0 0 6px">
  <p>description of his abilities was accurate. He worked quickly and efficiently, cheerfully handling questions and revisions within a short time frame. No hesitation in recommending him to anyone needing mechanical engineering work.</p>
  <p class="g-name" style="margin-left:-40px">Orrin Maddox</p><p class="g-role" style="margin-left:-40px">Client</p>
</div>

<article class="card active quote-card abs">
  <p class="quote">"5* Aldric was amazing. His communication was excellent, responded very quickly, started working on the project the same day I purchased, and problem solved every little detail with my design. He clearly knows about and has put in all his efforts to create a perfect design. I highly recommend his service and will use him again on my next project."</p>
  <p class="q-name">Renata Voss</p>
  <p class="q-role">Client</p>
</article>
<div class="avatar abs" style="left:640px;top:2886px;background:#eef0f6;opacity:.6"></div>
<div class="avatar abs" style="left:578px;top:2886px;background:linear-gradient(135deg,#8f949c,#4b4f57);border:4px solid #a9b9f3"></div>
<div class="avatar abs" style="left:527px;top:2886px;background:var(--white);border:4px solid var(--blue);color:var(--blue)">R</div>
<div class="dots abs"><span></span><span class="on"></span><span></span><span></span></div>

<section class="cta abs">
  <p class="cta-label abs">Curious What Else We Do</p>
  <p class="cta-title abs">Get in Touch to Discuss Your Next Project with Us</p>
  <a class="btn abs" style="left:470px;top:221px;width:260px;height:49px;background:#fff;color:var(--blue);border-radius:3px;box-shadow:5px 5px 0 #7f97ee" href="#">Tell Us About Your Ideas
    <svg width="16" height="12" viewBox="0 0 16 12"><path d="M1 6h13M9 1l5 5-5 5" fill="none" stroke="#2c55e6" stroke-width="1.6"/></svg></a>
</section>

<footer>
  <div class="brand abs" style="left:111px;top:3826px;gap:22px">
    <span class="brand-mark" style="width:104px;height:104px"></span><span class="brand-name" style="font-size:64px">valtorix</span>
  </div>
  <p class="foot-blurb abs">We offer a comprehensive mechanical and product design<br>service from initial concepts through to full volume production.</p>
  <nav class="foot-links abs"><a href="#">Home</a><a href="#">Work Portfolio</a><a href="#">Our Services</a><a href="#">Contact Us</a></nav>
  <p class="contact abs" style="left:636px">
    <svg width="18" height="14" viewBox="0 0 18 14"><rect x="1" y="1" width="16" height="12" fill="none" stroke="#2c55e6" stroke-width="1.5"/><path d="M1 1l8 7 8-7" fill="none" stroke="#2c55e6" stroke-width="1.5"/></svg>info@valtorix.design</p>
  <p class="contact abs" style="left:858px">
    <svg width="16" height="16" viewBox="0 0 16 16"><path d="M3 1l3 3-2 2c1 2 3 4 5 5l2-2 3 3-2 3C7 15 1 9 1 3z" fill="none" stroke="#2c55e6" stroke-width="1.4"/></svg>+44 (0) 7700 900412</p>
  <p class="copy abs">©Copyright 2025 Valtorix Design. All Rights Reserved.</p>
  <div class="follow abs">Follow us <span class="socials"><span></span><span></span><span></span><span></span></span></div>
</footer>

</body>
</html>
```